Advert for Services that we offer

Brimfold Haulage Ltd need an design to represent what we do in a modern way by showing an image with a brief description and the use of corporate logo the information we will proved vie a doc file and this is to be presented in a modern way. This design will be for print & web. we have done our own design and its not great i have put this in the file repository

Target Market(s)

Motor trade

Font styles to use
Sans Serif

Colors

Designer to choose colors to be used in the design.

Requirements
Must have
• Company colour scheme as per logo within the files uploaded.
• and a small boarder to isolate it from the rest of the articles.
Nice to have
• Modern font
Should not have
• Old style font

```html
<!DOCTYPE html>
<html lang="en">
<head>
<meta charset="utf-8">
<title>Brimfold Haulage Ltd – Product Testing &amp; Analysis</title>
<link rel="stylesheet" href="https://fonts.googleapis.com/css2?family=Oswald:wght@600;700&family=Jost:wght@300;500&display=swap">
<style>
  :root {
    --paper: #ffffff;
    --brand-blue: #1b75bc;
    --heading-grey: #c4c4c6;
    --list-grey: #d9d9db;
    --panel: rgba(38, 38, 40, 0.86);
    --rule: #bdbdbf;
  }
  * { margin: 0; padding: 0; box-sizing: border-box; }
  html, body { width: 1200px; height: 900px; overflow: hidden; background: var(--paper); }
  .advert { position: relative; width: 1200px; height: 900px; background: var(--paper); }

  .workshop-photo {
    position: absolute; left: 0; top: 87px; width: 1200px; height: 727px;
    background:
      radial-gradient(ellipse 240px 260px at 820px 600px, rgba(170, 70, 45, 0.85), transparent 70%),
      radial-gradient(ellipse 360px 420px at 1020px 400px, #3f4246, transparent 75%),
      linear-gradient(100deg, #a9a9a7 0%, #8e8d8a 35%, #b3b0ab 55%, #5a5c60 75%, #3d4044 100%);
  }

  .brand-block {
    position: absolute; left: 108px; top: 87px; width: 293px; height: 163px;
    background: var(--paper);
    display: flex; align-items: center; justify-content: center; gap: 10px;
  }
  .brand-mark { width: 16px; height: 16px; background: var(--brand-blue); }
  .brand-name {
    font-family: "Jost", sans-serif; font-weight: 500; font-size: 21px;
    color: var(--brand-blue); letter-spacing: 0.5px;
  }

  .services-panel {
    position: absolute; left: 53px; top: 296px; width: 547px; height: 518px;
    background: var(--panel);
  }
  .panel-heading { position: absolute; left: 103px; top: 48px; }
  .heading-rule {
    position: absolute; left: 0; top: 52px; width: 154px; height: 2px; background: var(--rule);
  }
  .heading-title {
    position: absolute; left: 160px; top: -8px; white-space: nowrap;
    font-family: "Oswald", sans-serif; font-weight: 700; font-size: 56px;
    line-height: 1; letter-spacing: 4px; color: var(--heading-grey);
  }
  .heading-sub {
    position: absolute; left: 0; top: 62px; white-space: nowrap;
    font-family: "Oswald", sans-serif; font-weight: 600; font-size: 31px;
    line-height: 1; letter-spacing: 2.3px; color: var(--brand-blue);
  }

  .service-list { position: absolute; left: 55px; top: 208px; list-style: none; }
  .service-item {
    display: flex; align-items: center; height: 48px;
    font-family: "Jost", sans-serif; font-weight: 300; font-size: 36px;
    color: var(--list-grey); white-space: nowrap;
  }
  .service-chevron { width: 25px; height: 18px; margin-right: 23px; flex: none; display: block; }
</style>
</head>
<body>
<main class="advert">
  <div class="workshop-photo" role="img" aria-label="Technician in safety glasses measuring the bore of a red cast hub with a digital gauge in a workshop with a red workbench"></div>

  <div class="brand-block">
    <span class="brand-mark"></span>
    <span class="brand-name">Brimfold Haulage Ltd</span>
  </div>

  <section class="services-panel">
    <div class="panel-heading">
      <span class="heading-rule"></span>
      <h1 class="heading-title">KORVANE</h1>
      <h2 class="heading-sub">Product Testing &amp; Analysis</h2>
    </div>

    <ul class="service-list">
      <li class="service-item"><svg class="service-chevron" width="25" height="18" viewBox="0 0 25 18"><path d="M2 2l7 7-7 7M14 2l7 7-7 7" fill="none" stroke="#1b75bc" stroke-width="3.5"/></svg>Metallurgical Testing</li>
      <li class="service-item"><svg class="service-chevron" width="25" height="18" viewBox="0 0 25 18"><path d="M2 2l7 7-7 7M14 2l7 7-7 7" fill="none" stroke="#1b75bc" stroke-width="3.5"/></svg>Bearing Pre-load Testing</li>
      <li class="service-item"><svg class="service-chevron" width="25" height="18" viewBox="0 0 25 18"><path d="M2 2l7 7-7 7M14 2l7 7-7 7" fill="none" stroke="#1b75bc" stroke-width="3.5"/></svg>Bore Measurement</li>
      <li class="service-item"><svg class="service-chevron" width="25" height="18" viewBox="0 0 25 18"><path d="M2 2l7 7-7 7M14 2l7 7-7 7" fill="none" stroke="#1b75bc" stroke-width="3.5"/></svg>New Product Evaluation</li>
      <li class="service-item"><svg class="service-chevron" width="25" height="18" viewBox="0 0 25 18"><path d="M2 2l7 7-7 7M14 2l7 7-7 7" fill="none" stroke="#1b75bc" stroke-width="3.5"/></svg>Product Analysis &amp; Report</li>
    </ul>
  </section>
</main>
</body>
</html>
```